Support People to improve their image and well-being by provided personalised advise

We need a design for business cards that could be used for production on plano press. We build a new business in our region for advising mostly women (also men though) on style embracing several aspects including fashion, style, self-confidence and ultimately your internal and external image. The business card should be "classy", "french-style". The business is located in the french -speaking part of Switzerland, close to France. The name of the company is Lomu Grace

Target Market(s)

Service fees won't be cheap (medium to premium) thus we target mid-class to upper-class women (1st target) and men (2nd target)

Industry/Entity Type

Life Coaching

Contact Information for Business Card

Conseil en Image

+41 76 418 63 07
tovasel@lomu-grace.example
linkedin.example/in/sel-moran-tova

Logo Text

Lomu Grace

Colors

Designer to choose colors to be used in the design.

```html
<!DOCTYPE html>
<html lang="fr">
<head>
<meta charset="utf-8">
<title>Lomu Grace – Cartes de visite</title>
<link rel="stylesheet" href="https://fonts.googleapis.com/css2?family=Jost:wght@300;400;500&family=Kaushan+Script&display=swap">
<style>
  :root{
    --backdrop:#bfbfbf;
    --card:#363a3d;
    --gold:#c9a27a;
    --gold-light:#dcc0a0;
    --silver:#c4c4c4;
    --text-light:#d8d8d8;
  }
  *{margin:0;padding:0;box-sizing:border-box;}
  html,body{width:1200px;height:576px;overflow:hidden;background:var(--backdrop);}
  .canvas{position:relative;width:1200px;height:576px;}
  .card{
    position:absolute;top:138px;width:484px;height:292px;
    background:var(--card);border-radius:13px;
  }
  .card--front{left:82px;}
  .card--back{left:602px;}
  .brand-mark{
    position:absolute;border-radius:50%;
    background:linear-gradient(160deg,var(--gold) 0%,var(--gold-light) 100%);
  }
  .brand-name{
    position:absolute;font-family:"Jost",sans-serif;font-weight:400;
    color:var(--silver);letter-spacing:.18em;white-space:nowrap;line-height:1;
  }
  .card--front .brand-mark{left:212px;top:96px;width:60px;height:60px;}
  .card--front .brand-name{left:0;width:484px;text-align:center;top:187px;font-size:27px;}
  .holder-name{
    position:absolute;left:28px;top:38px;font-family:"Kaushan Script",cursive;
    font-size:23px;color:var(--gold);line-height:1.2;
  }
  .holder-role{
    position:absolute;left:28px;top:69px;font-family:"Jost",sans-serif;
    font-weight:400;font-size:12.5px;color:var(--text-light);
  }
  .contact-list{position:absolute;left:28px;top:208px;list-style:none;}
  .contact-item{
    display:flex;align-items:center;height:17.5px;font-family:"Jost",sans-serif;
    font-weight:300;font-size:13px;color:var(--text-light);
  }
  .contact-icon{width:11px;height:11px;margin-right:14px;fill:var(--text-light);}
  .card--back .brand-mark{left:326px;top:148px;width:56px;height:56px;}
  .card--back .brand-name{right:36px;top:236px;font-size:23px;}
</style>
</head>
<body>
<main class="canvas">
  <section class="card card--front" aria-label="Recto">
    <span class="brand-mark" aria-hidden="true"></span>
    <p class="brand-name">LOMU GRACE</p>
  </section>

  <section class="card card--back" aria-label="Verso">
    <h1 class="holder-name">Sel Moran Tova</h1>
    <p class="holder-role">Managing Director</p>
    <ul class="contact-list">
      <li class="contact-item">
        <svg class="contact-icon" viewBox="0 0 12 12" aria-hidden="true"><path d="M1 3.5C1 2 2.5 1.5 6 1.5S11 2 11 3.5V5H8.5V4h-5v1H1z"/><rect x="2" y="6" width="8" height="5" rx="1"/></svg>
        +41 76 418 63 07
      </li>
      <li class="contact-item">
        <svg class="contact-icon" viewBox="0 0 12 12" aria-hidden="true"><rect x="0.5" y="2" width="11" height="8"/><path d="M1 2.5l5 4 5-4" fill="none" stroke="#363a3d" stroke-width="1.2"/></svg>
        tovasel@lomu-grace.example
      </li>
      <li class="contact-item">
        <svg class="contact-icon" viewBox="0 0 12 12" aria-hidden="true"><circle cx="6" cy="6" r="5.5"/><path d="M0.5 6h11M6 0.5v11M6 0.8c-3 3-3 7.4 0 10.4M6 0.8c3 3 3 7.4 0 10.4" fill="none" stroke="#363a3d" stroke-width="0.9"/></svg>
        www.lomu-grace.example
      </li>
    </ul>
    <span class="brand-mark" aria-hidden="true"></span>
    <p class="brand-name">LOMU GRACE</p>
  </section>
</main>
</body>
</html>
```